Business Card Design for Training Business

Clear Path Coaching is a new business that delivers training and other services with a focus on topics related to mental health and wellbeing, for example, Wellmind Response Course, Resilience etc. We have a strong focus on evidence-based psychology and neuroscience. I have a logo which I will upload with the brief, so please consider colours that work well with the logo.
Target Market(s)
Adults, workplaces (particularly government and not-for-profits)
Industry/Entity Type
Business
Contact Information for Business Card
Head Strong TrainingSamantha SellwoodDirector0438 770 850sam@headstrongtraining.com.auwww.headstrongtraining.com.au

```html
<!DOCTYPE html>
<html lang="en">
<head>
<meta charset="utf-8">
<title>Clear Path Coaching — Business Card</title>
<link href="https://fonts.googleapis.com/css2?family=Questrial&display=swap" rel="stylesheet">
<style>
  :root {
    --backdrop: #3a3a3a;
    --card-white: #f7f7f7;
    --teal: #22b5bb;
    --teal-deep: #1ea9af;
    --ink: #3c3c3c;
    --brand-grey: #6b6b6b;
    --white: #ffffff;
  }
  * { margin: 0; padding: 0; box-sizing: border-box; }
  html, body {
    width: 1200px;
    height: 750px;
    overflow: hidden;
    background: var(--backdrop);
    font-family: "Questrial", "Century Gothic", sans-serif;
  }
  .canvas {
    position: relative;
    width: 1200px;
    height: 750px;
  }
  .card {
    position: absolute;
    left: 371px;
    width: 461px;
    height: 263px;
    border-radius: 14px;
    overflow: hidden;
  }
  .card--front { top: 106px; background: var(--card-white); }
  .card--back { top: 387px; background: var(--teal); }

  .name-band {
    position: absolute;
    left: 0;
    top: 26px;
    width: 350px;
    height: 68px;
    background: var(--teal);
  }
  .brand-dot {
    position: absolute;
    left: 316px;
    top: 26px;
    width: 68px;
    height: 68px;
    border-radius: 50%;
    background: var(--teal-deep);
    border: 2px solid var(--white);
  }
  .holder {
    position: absolute;
    left: 27px;
    top: 40px;
    color: var(--white);
  }
  .holder__name { font-size: 19px; letter-spacing: 0.3px; line-height: 1.1; }
  .holder__role { font-size: 14px; line-height: 1.3; }

  .brand {
    position: absolute;
    right: 26px;
    top: 103px;
    text-align: center;
    color: var(--brand-grey);
    font-weight: 400;
  }
  .brand__main { font-size: 20px; letter-spacing: 2.5px; line-height: 1.1; }
  .brand__sub { font-size: 10px; letter-spacing: 5px; margin-top: 4px; padding-left: 5px; }

  .contacts {
    position: absolute;
    left: 30px;
    top: 186px;
    list-style: none;
    color: var(--ink);
    font-size: 12px;
  }
  .contacts li {
    display: flex;
    align-items: center;
    gap: 6px;
    height: 17.5px;
  }
  .contacts svg { width: 11px; height: 11px; flex: none; }

  .back-mark {
    position: absolute;
    left: 50%;
    top: 62px;
    transform: translateX(-50%);
    width: 90px;
    height: 90px;
    border-radius: 50%;
    border: 1.5px solid var(--white);
  }
  .back-brand {
    position: absolute;
    left: 0;
    right: 0;
    top: 166px;
    text-align: center;
    color: var(--white);
    font-size: 14px;
    letter-spacing: 3px;
  }
  .back-url {
    position: absolute;
    left: 0;
    right: 0;
    top: 227px;
    text-align: center;
    color: var(--white);
    font-size: 12px;
  }
</style>
</head>
<body>
<main class="canvas">
  <section class="card card--front" aria-label="Card front">
    <div class="name-band"></div>
    <div class="brand-dot"></div>
    <div class="holder">
      <p class="holder__name">Rebecca Tanfield</p>
      <p class="holder__role">Director</p>
    </div>
    <div class="brand">
      <p class="brand__main">CLEAR PATH</p>
      <p class="brand__sub">COACHING</p>
    </div>
    <ul class="contacts">
      <li>
        <svg viewBox="0 0 12 12" aria-hidden="true"><path d="M2.5 1 L4.6 1 L5.3 3.6 L4 4.7 C4.7 6.2 5.8 7.3 7.3 8 L8.4 6.7 L11 7.4 L11 9.5 C11 10.4 10.3 11 9.5 11 C5 11 1 7 1 2.5 C1 1.7 1.6 1 2.5 1 Z" fill="var(--teal)"/></svg>
        0491 362 517
      </li>
      <li>
        <svg viewBox="0 0 12 12" aria-hidden="true"><rect x="0.5" y="2.5" width="11" height="7.5" fill="var(--teal)"/><path d="M0.5 2.5 L6 6.8 L11.5 2.5" fill="none" stroke="var(--white)" stroke-width="0.9"/></svg>
        bec@clearpathcoaching.example.au
      </li>
      <li>
        <svg viewBox="0 0 12 12" aria-hidden="true"><circle cx="6" cy="6" r="5.5" fill="var(--teal)"/><path d="M6 0.5 V11.5 M0.5 6 H11.5 M6 0.5 C3 3.5 3 8.5 6 11.5 M6 0.5 C9 3.5 9 8.5 6 11.5" fill="none" stroke="var(--white)" stroke-width="0.7"/></svg>
        www.clearpathcoaching.example.au
      </li>
    </ul>
  </section>

  <section class="card card--back" aria-label="Card back">
    <div class="back-mark"></div>
    <p class="back-brand">CLEAR PATH COACHING</p>
    <p class="back-url">www.clearpathcoaching.example.au</p>
  </section>
</main>
</body>
</html>
```